Creation of an elegant and modern turnkey Shopify website

Hello,

We are a new company specializing in the sale of above-ground pools. We want to create a turnkey website, ideally using Shopify. For now, we need a "showcase" site, not an e-commerce platform, with four tabs:

Home Page (an overall presentation of the company)
Our Products (an overview of all the above-ground pools we sell)
Our Projects (a page inspired by Instagram to showcase photos of our future projects)
Contact (a page with all our contact information and a contact form)

We are looking to create a highly visual, elegant, and modern website with vibrant splashes of color. We will provide the text, photos (along with instructions on where to place them on each page), and all other necessary information as attachments.

Thank you in advance for your proposals!

The Brisa Lagoon Team

Target Market(s)

Targeted at Swiss customers (a translator will need to be installed for different languages)

Industry/Entity Type

Sale of customised above-ground pools

Coding

Coded - Design and coding required

Font styles to use
Sans Serif

Colors
0094D4
00A9DD
6FCCEA
C7EBF8
E9F6FB
00AB8E
00BBA5
67D7C9
C6EFE9
E9F9F6

Requirements
Must have
• A stunning, elegant and modern look
Nice to have
• Inspiration from the colors of our logo throughout the site, but in an elegant way
Should not have
• An overly classic look for swimming pool sites

```html
<!DOCTYPE html>
<html lang="en">
<head>
<meta charset="utf-8">
<title>Brisa Lagoon – Premium Above-Ground Pools</title>
<link rel="stylesheet" href="https://fonts.googleapis.com/css2?family=Lato:wght@400;700;900&family=Catamaran:wght@300;400;500&family=Poppins:wght@400&display=swap">
<style>
  :root {
    --blue-deep: #0094D4;
    --blue: #00A9DD;
    --blue-soft: #6FCCEA;
    --blue-pale: #C7EBF8;
    --blue-mist: #E9F6FB;
    --teal: #00AB8E;
    --teal-bright: #00BBA5;
    --ink: #161616;
    --text: #2e2e2e;
    --footer: #2b2b2b;
    --white: #ffffff;
  }
  * { box-sizing: border-box; margin: 0; padding: 0; }
  html, body { width: 1200px; height: 3338px; overflow: hidden; background: var(--white); }
  body { position: relative; font-family: "Lato", sans-serif; color: var(--text); }
  .abs { position: absolute; }

  /* header */
  .brand { left: 74px; top: 34px; font-family: "Catamaran", sans-serif; font-weight: 300; color: var(--blue); font-size: 28px; line-height: 30px; letter-spacing: 1px; text-transform: uppercase; }
  .nav { top: 57px; right: 75px; display: flex; gap: 42px; font-family: "Poppins", sans-serif; font-size: 14px; letter-spacing: .3px; }
  .nav a { color: var(--ink); text-decoration: none; }
  .nav a.active { color: var(--blue-deep); border-bottom: 1.5px solid var(--blue-deep); padding-bottom: 2px; }

  /* hero */
  .hero-title { left: 74px; top: 150px; width: 540px; font-weight: 900; font-size: 47px; line-height: 50.5px; color: var(--ink); text-transform: uppercase; letter-spacing: .3px; white-space: nowrap; }
  .hero-sub { left: 74px; top: 414px; width: 470px; font-weight: 700; font-size: 22.5px; line-height: 30px; color: var(--blue-deep); }
  .hero-text { left: 74px; top: 483px; width: 530px; font-size: 14.3px; line-height: 25.7px; white-space: nowrap; }
  .btn { left: 74px; top: 640px; width: 152px; height: 46px; background: var(--teal-bright); color: var(--white); font-size: 14.5px; display: flex; align-items: center; justify-content: center; letter-spacing: .3px; }
  .photo { position: absolute; }
  .arrow { top: 377px; }

  /* why */
  .section-title { font-family: "Catamaran", sans-serif; font-weight: 400; font-size: 42px; line-height: 40px; color: var(--ink); }
  .accordion-item { left: 616px; width: 510px; background: var(--blue-mist); padding: 0 24px; }
  .accordion-item h3 { font-family: "Catamaran", sans-serif; font-weight: 500; font-size: 21px; color: var(--ink); display: flex; justify-content: space-between; align-items: center; height: 62px; }
  .accordion-item.open h3 { color: var(--blue-deep); height: 54px; padding-top: 10px; }
  .accordion-item p { font-size: 14.5px; line-height: 24px; }

  .body-text { font-size: 14.3px; line-height: 27.2px; white-space: nowrap; }

  .feature-card { left: 74px; top: 2089px; width: 329px; height: 360px; background: var(--blue); color: var(--white); padding: 50px 24px 0; }
  .feature-card .section-title { color: var(--white); }
  .feature-card p { margin-top: 28px; font-size: 14px; line-height: 27.2px; }
  .feature-card strong { display: block; margin-top: 6px; font-size: 16.5px; }

  /* contact band */
  .contact-band { left: 0; top: 2536px; width: 1200px; height: 376px; background: radial-gradient(ellipse at 20% 30%, #25b6e8 0%, transparent 45%), radial-gradient(ellipse at 85% 80%, #0579b3 0%, transparent 50%), linear-gradient(135deg, #0aa3de, #0093d0); color: var(--white); text-align: center; }
  .contact-band h2 { margin-top: 106px; font-family: "Catamaran", sans-serif; font-weight: 400; font-size: 44px; }
  .contact-band p { margin-top: 18px; font-family: "Catamaran", sans-serif; font-size: 21px; line-height: 32.5px; }

  /* footer */
  .footer { left: 0; top: 2912px; width: 1200px; height: 426px; background: var(--footer); color: var(--white); }
  .footer-links { left: 74px; top: 60px; font-family: "Poppins", sans-serif; }
  .footer-links h4 { font-weight: 400; font-size: 18px; margin-bottom: 14px; }
  .footer-links a { display: block; color: var(--white); text-decoration: none; font-size: 13px; line-height: 37px; }
  .footer-brand { left: 616px; top: 70px; font-family: "Catamaran", sans-serif; font-weight: 300; color: var(--blue); font-size: 34px; line-height: 40px; letter-spacing: 1px; text-transform: uppercase; }
  .tagline { left: 770px; top: 98px; font-family: "Catamaran", sans-serif; font-size: 21.5px; white-space: nowrap; }
  .socials { left: 616px; top: 208px; display: flex; gap: 20px; }
  .socials span { width: 22px; height: 22px; border-radius: 50%; background: var(--white); }
  .rule { left: 74px; top: 288px; width: 1052px; height: 1px; background: #4a4a4a; }
  .cards { left: 463px; top: 341px; display: flex; gap: 12px; }
  .cards span { width: 36px; height: 22px; border-radius: 3px; background: #e8e8e8; }
  .copyright { left: 0; top: 376px; width: 1200px; text-align: center; font-family: "Poppins", sans-serif; font-size: 12px; color: #d0d0d0; }
</style>
</head>
<body>

<header>
  <div class="abs brand">Brisa<br>Lagoon</div>
  <nav class="abs nav">
    <a class="active" href="#">HOME</a>
    <a href="#">OUR PRODUCTS</a>
    <a href="#">OUR WORKS</a>
    <a href="#">CONTACT US</a>
  </nav>
</header>

<section class="hero">
  <h1 class="abs hero-title">Transform your<br>garden with our<br>premium<br>above-ground<br>pools!</h1>
  <p class="abs hero-sub">Achieve your dreams with our custom,<br>tailor-made above-ground pools.</p>
  <p class="abs hero-text">Imagine an exceptional relaxation and leisure space right in your own<br>backyard. With our unparalleled expertise and commitment to excellence, we<br>create above-ground pools that exceed all expectations. Our exclusive,<br>custom-designed models are crafted to combine style, durability, and<br>innovation, offering a unique and refined experience.</p>
  <a class="abs btn">READ MORE</a>
  <svg class="abs arrow" style="left:586px" width="16" height="24" viewBox="0 0 16 24"><path d="M12 2 L3 12 L12 22" fill="none" stroke="#161616" stroke-width="2"/></svg>
  <div class="photo" role="img" aria-label="Rectangular above-ground frame pool on a green lawn in a fenced garden" style="left:616px;top:144px;width:510px;height:557px;background:linear-gradient(180deg,#3f6b3a 0%,#6c8a52 18%,#2f8fd8 35%,#bfc6cc 55%,#9aa3aa 70%,#2c7fd0 82%,#6a9a3c 100%);"></div>
  <svg class="abs arrow" style="left:1140px" width="16" height="24" viewBox="0 0 16 24"><path d="M4 2 L13 12 L4 22" fill="none" stroke="#161616" stroke-width="2"/></svg>
</section>

<section class="why">
  <h2 class="abs section-title" style="left:74px;top:804px;">Why Choose Our<br>Above-Ground Pools?</h2>
  <div class="photo" role="img" aria-label="Man setting up a round above-ground pool in a flowering garden" style="left:74px;top:915px;width:513px;height:533px;background:linear-gradient(180deg,#3d5e2c 0%,#6a5aa8 20%,#5d7a3a 35%,#b8bcc2 48%,#a9adb3 85%,#d9dbdd 100%);"></div>

  <div class="abs accordion-item open" style="top:915px;height:118px;">
    <h3>Superior Quality
      <svg width="14" height="10" viewBox="0 0 14 10"><path d="M2 2 L7 7 L12 2" fill="none" stroke="#0094D4" stroke-width="2.4"/></svg>
    </h3>
    <p>Each pool is constructed with high-quality materials, ensuring exceptional durability and strength.</p>
  </div>
  <div class="abs accordion-item" style="top:1052px;">
    <h3>Elegant Design <svg width="10" height="14" viewBox="0 0 10 14"><path d="M2 2 L7 7 L2 12" fill="none" stroke="#0094D4" stroke-width="2.4"/></svg></h3>
  </div>
  <div class="abs accordion-item" style="top:1134px;">
    <h3>Custom and Tailor-Made <svg width="10" height="14" viewBox="0 0 10 14"><path d="M2 2 L7 7 L2 12" fill="none" stroke="#0094D4" stroke-width="2.4"/></svg></h3>
  </div>
  <div class="abs accordion-item" style="top:1216px;">
    <h3>Easy Installation <svg width="10" height="14" viewBox="0 0 10 14"><path d="M2 2 L7 7 L2 12" fill="none" stroke="#0094D4" stroke-width="2.4"/></svg></h3>
  </div>
</section>

<section class="services">
  <div class="photo" role="img" aria-label="Technician rolling a blue solar cover beside a pool" style="left:74px;top:1546px;width:345px;height:451px;background:linear-gradient(160deg,#5aa9d8 0%,#c9302b 35%,#2d6fc7 60%,#8f9296 100%);"></div>
  <div class="photo" role="img" aria-label="Swimmer floating on an inflatable ring in a round pool" style="left:419px;top:1546px;width:347px;height:451px;background:linear-gradient(160deg,#4fc3ec 0%,#2aa2e2 45%,#e9b7c9 60%,#2b8fd6 80%,#6aa34a 100%);"></div>
  <h2 class="abs section-title" style="left:793px;top:1638px;">Personalized<br>Services</h2>
  <p class="abs body-text" style="left:793px;top:1737px;">We understand that every garden and client is<br>unique. That's why we offer personalized services,<br>from design to installation and after-sales<br>support. Our team of experts is here to answer all<br>your questions and guide you throughout<br>your project.</p>
</section>

<section class="satisfaction">
  <div class="abs feature-card">
    <h2 class="section-title">Guaranteed<br>Satisfaction</h2>
    <p>Your satisfaction is our top priority.<br>We are committed to providing you with exceptional service and the highest quality products. Join our community of satisfied customers who are already enjoying their custom above-ground pools.</p>
    <strong>10-Year Warranty!</strong>
  </div>
  <div class="photo" role="img" aria-label="Round patterned soft-sided pool on a terrace with potted plants" style="left:437px;top:2089px;width:329px;height:360px;background:linear-gradient(180deg,#eef0ee 0%,#7a9a60 22%,#8ab9c9 45%,#3a3f44 75%,#2a2d30 100%);"></div>
  <div class="photo" role="img" aria-label="Round pool beside a white balustrade and a tropical plant" style="left:798px;top:2089px;width:329px;height:360px;background:linear-gradient(180deg,#e8e6e2 0%,#d9d6d0 25%,#8fb6c4 50%,#35393d 80%,#2a2d30 100%);"></div>
</section>

<section class="abs contact-band" role="region" aria-label="Contact call to action on a rippling water background">
  <h2>Contact Us Today</h2>
  <p>Don't wait any longer to transform your garden into a wellness oasis. Contact us today to<br>discover our range of customizable above-ground pools and get a tailored quote.<br>Dive into a world of infinite possibilities with Brisa Lagoon.</p>
</section>

<footer class="abs footer">
  <div class="abs footer-links">
    <h4>QUICK LINKS</h4>
    <a href="#">Home</a>
    <a href="#">Our Products</a>
    <a href="#">Our Works</a>
    <a href="#">Contact Us</a>
  </div>
  <div class="abs footer-brand">Brisa<br>Lagoon</div>
  <p class="abs tagline">We Bring Your Pool Dreams to Life!</p>
  <div class="abs socials"><span></span><span></span><span></span><span></span><span></span></div>
  <div class="abs rule"></div>
  <div class="abs cards"><span></span><span></span><span></span><span></span><span></span><span></span></div>
  <p class="abs copyright">Copyright © 2024. Company Name All Right Reserved</p>
</footer>

</body>
</html>
```